Brimlow Plumbing Solutions

This is for my new plumbing company, I have attached an example of what I’m going for but want it to look better.

Target Market(s)

Home owners, real estate, etc.

Industry/Entity Type

Plumbing

Font styles to use
Other font styles liked:
• As per my logo and other examples uploaded

Colors

Designer to choose colors to be used in the design.

Requirements
Must have
• Must include my logo provided and similar to my flyer I have attached but better

```html
<!DOCTYPE html>
<html lang="en">
<head>
<meta charset="utf-8">
<title>Brimlow Plumbing Solutions – Flyer</title>
<link rel="stylesheet" href="https://fonts.googleapis.com/css2?family=Montserrat:wght@600;700;800&family=Arimo:wght@400;500&display=swap">
<style>
  :root {
    --navy: #0d2c5e;
    --navy-deep: #0a2250;
    --blue: #2f8fd6;
    --blue-light: #4aa6e8;
    --white: #ffffff;
    --ink: #1b2433;
    --page: #e6e6e6;
  }
  * { margin: 0; padding: 0; box-sizing: border-box; }
  html, body { width: 1200px; height: 1200px; overflow: hidden; background: var(--page); }
  .flyer {
    position: absolute; left: 280px; top: 102px;
    width: 640px; height: 996px;
    background: var(--navy);
    overflow: hidden;
    font-family: "Arimo", Arial, sans-serif;
    color: var(--ink);
  }
  .flyer-shapes { position: absolute; inset: 0; width: 640px; height: 996px; }
  .hero-art {
    position: absolute; left: 316px; top: 37px; width: 294px; height: 305px;
    background: radial-gradient(ellipse at 45% 55%, #1f4f95 0%, #15397a 55%, rgba(13,44,94,0) 80%);
  }
  .brand { position: absolute; left: 44px; top: 116px; color: var(--white); font-family: "Montserrat", Arial, sans-serif; }
  .brand-name { font-size: 60px; font-weight: 800; letter-spacing: 1px; line-height: 1; }
  .brand-sub {
    font-size: 19px; font-weight: 600; margin-top: 10px; padding-bottom: 6px;
    border-bottom: 1.5px solid rgba(255,255,255,.75); display: inline-block;
  }
  .brand-tagline { font-family: "Arimo", Arial, sans-serif; font-size: 15px; margin-top: 8px; }
  .section-brand {
    position: absolute; left: 44px; top: 384px;
    font-family: "Montserrat", Arial, sans-serif; font-weight: 800; font-size: 28px; color: var(--navy);
  }
  .service-col { position: absolute; list-style: none; }
  .service-col h2 {
    font-family: "Montserrat", Arial, sans-serif; font-weight: 700; font-size: 24px; color: var(--navy);
    margin-bottom: 14px;
  }
  .service-col li { display: flex; align-items: center; gap: 10px; font-size: 20px; height: 38px; }
  .service-col li.plain { padding-left: 8px; }
  .expertise { left: 40px; top: 438px; }
  .what-we-do { left: 361px; top: 480px; }
  .icon { width: 26px; height: 26px; flex: none; }
  .highlight-title {
    position: absolute; left: 52px; top: 756px;
    font-family: "Montserrat", Arial, sans-serif; font-weight: 700; font-size: 21px; color: var(--white);
  }
  .offer {
    position: absolute; left: 26px; top: 796px; width: 208px; height: 112px;
    clip-path: polygon(12% 0, 88% 0, 100% 50%, 88% 100%, 12% 100%, 0 50%);
    background: var(--blue);
    color: var(--white); text-align: center;
    display: flex; flex-direction: column; justify-content: center;
  }
  .offer-lead, .offer-tail { font-size: 19px; font-weight: 500; line-height: 1.15; }
  .offer-value { font-family: "Montserrat", Arial, sans-serif; font-size: 34px; font-weight: 700; line-height: 1.1; }
  .contact { position: absolute; left: 353px; top: 852px; width: 255px; color: var(--white); }
  .contact-title {
    font-family: "Montserrat", Arial, sans-serif; font-weight: 700; font-size: 31px;
    padding-left: 40px; padding-bottom: 12px; border-bottom: 1.5px solid rgba(255,255,255,.8);
  }
  .contact-codes { font-size: 18px; font-weight: 500; margin-top: 14px; padding-left: 20px; letter-spacing: .5px; }
</style>
</head>
<body>
<main class="flyer">
  <svg class="flyer-shapes" viewBox="0 0 640 996" aria-hidden="true">
    <!-- top right accent stripes -->
    <polygon points="560,0 640,0 640,40 600,0" fill="#4aa6e8"/>
    <polygon points="520,0 545,0 640,95 640,120" fill="#2f8fd6"/>
    <polygon points="600,60 640,100 640,150 580,90" fill="#1f6fc0"/>
    <!-- left diagonal stripes -->
    <g fill="#2f8fd6">
      <polygon points="0,260 8,260 70,330 62,330"/>
      <polygon points="0,285 8,285 50,335 42,335"/>
      <polygon points="0,310 8,310 30,338 22,338"/>
    </g>
    <!-- light band above panel -->
    <polygon points="0,330 105,292 190,345 640,345 640,408 330,408 300,362 165,362 105,322 0,358" fill="#2f8fd6"/>
    <polygon points="300,350 640,350 640,368 312,368" fill="#4aa6e8"/>
    <!-- white services panel -->
    <polygon points="0,362 105,326 165,366 298,366 328,412 640,412 640,738 0,738" fill="#ffffff"/>
    <!-- bottom accents -->
    <polygon points="400,738 520,738 640,668 640,640" fill="#2f8fd6"/>
    <polygon points="470,760 640,690 640,712 500,768" fill="#4aa6e8"/>
    <g fill="#2f8fd6">
      <polygon points="0,880 10,880 130,996 118,996"/>
      <polygon points="0,910 10,910 100,996 88,996"/>
      <polygon points="0,940 10,940 70,996 58,996"/>
    </g>
    <polygon points="180,996 250,930 290,930 225,996" fill="#1f6fc0"/>
  </svg>

  <div class="hero-art" role="img" aria-label="Large decorative illustration area in navy and blue"></div>

  <header class="brand">
    <div class="brand-name">BRIMLOW</div>
    <div class="brand-sub">PLUMBING SOLUTIONS</div>
    <div class="brand-tagline">Reliable Plumbing. Real Solutions.</div>
  </header>

  <div class="section-brand">BRIMLOW</div>

  <ul class="service-col expertise">
    <h2>Our Expertise</h2>
    <li class="plain">Emergency Plumbing</li>
    <li><svg class="icon" viewBox="0 0 26 26"><circle cx="13" cy="13" r="13" fill="#2f8fd6"/><path d="M7 10h12l-2 8H9z" fill="#fff"/></svg>Blocked Drains &amp; Sewer</li>
    <li><svg class="icon" viewBox="0 0 26 26"><circle cx="13" cy="13" r="13" fill="#2f8fd6"/><rect x="9" y="7" width="8" height="12" rx="2" fill="#fff"/></svg>Hot Water Systems</li>
    <li><svg class="icon" viewBox="0 0 26 26"><circle cx="13" cy="13" r="13" fill="#2f8fd6"/><path d="M13 6c3 4 5 6 5 9a5 5 0 0 1-10 0c0-3 2-5 5-9z" fill="#fff"/></svg>Gas Fitting &amp; Maintenance</li>
    <li><svg class="icon" viewBox="0 0 26 26"><circle cx="13" cy="13" r="13" fill="#2f8fd6"/><path d="M13 7c2.5 3.5 4 5.5 4 7.5a4 4 0 0 1-8 0c0-2 1.5-4 4-7.5z" fill="#fff"/></svg>Leaking Fixtures</li>
  </ul>

  <ul class="service-col what-we-do">
    <h2>What We Do</h2>
    <li><svg class="icon" viewBox="0 0 26 26"><circle cx="13" cy="13" r="13" fill="#2f8fd6"/><path d="M8 18l8-8M14 8l4 4" stroke="#fff" stroke-width="3" stroke-linecap="round"/></svg>Hot Water Systems</li>
    <li><svg class="icon" viewBox="0 0 26 26"><circle cx="13" cy="13" r="13" fill="#2f8fd6"/><path d="M13 6a4.5 4.5 0 0 1 4.5 4.5C17.5 14 13 20 13 20s-4.5-6-4.5-9.5A4.5 4.5 0 0 1 13 6z" fill="#fff"/><circle cx="13" cy="10.5" r="1.6" fill="#2f8fd6"/></svg>Fixture Maintenance</li>
    <li><svg class="icon" viewBox="0 0 26 26"><circle cx="13" cy="13" r="13" fill="#2f8fd6"/><rect x="7" y="10" width="12" height="9" rx="1.5" fill="#fff"/><rect x="10.5" y="7" width="5" height="3" fill="#fff"/></svg>Camera &amp; Locating</li>
    <li><svg class="icon" viewBox="0 0 26 26"><circle cx="13" cy="13" r="13" fill="#2f8fd6"/><circle cx="13" cy="13" r="5" fill="none" stroke="#fff" stroke-width="3"/></svg>TMV Maintenance</li>
  </ul>

  <div class="highlight-title">FEATURE HIGHLIGHT</div>
  <div class="offer">
    <span class="offer-lead">Mention this flyer for</span>
    <span class="offer-value">15% OFF</span>
    <span class="offer-tail">Your first service!</span>
  </div>

  <section class="contact">
    <div class="contact-title">CONTACT</div>
    <div class="contact-codes">#0004C93 &nbsp;#E6E6E6</div>
  </section>
</main>
</body>
</html>
```